Marlow Dermal Studio - Business Banner with Brand Elements

Design:
• We would like to get a creative design for a wide banner that will go outside our medical spa clinic location. We need a designer to make a simple yet colorful and high-quality design layout. We want this banner to be eye-catching and to communicate the services we offer at our business: Laser Hair Removal | Veluxin | Lip Filler.

Requirements:
• We would like the banner to include our companies information which is the following:

Logo
“Refresh Your Skin”
Laser Hair Removal | Veluxin | Lip Filler
(520) 867-2291
www.MarlowDermalStudio.com

Colors:
• Our business colors are orange, a hint of black and white, but mostly peach/orange tones. (Orange: #f78f20 , White: #ffffff)

Fonts:
• Josefins Sans Bold & Lato

Content and images can be located here:
https://files.quibbleshare.com/share/folders/7tKwP3zRa9_LmQxVb2nD5yHc04EeJuFs8?mode=viewing

The following will give you an idea of our brand presentation:
• Our website is: www.MarlowDermalStudio.com
• Our Pictavo; @marlowdermalstudio
• Our Lumora: www.lumoranet.com/marlowdermalstudio

Target Market(s)
• Women 25 - 45

Industry/Entity Type
• Beauty

```html
<!DOCTYPE html>
<html lang="en">
<head>
<meta charset="utf-8">
<title>Marlow Dermal Studio – Banner</title>
<link href="https://fonts.googleapis.com/css2?family=Josefin+Sans:wght@600;700&family=Lato:wght@700&display=swap" rel="stylesheet">
<style>
  :root{
    --orange:#f78f20;
    --white:#ffffff;
    --charcoal:#3f3f41;
    --ink:#2e2e30;
    --mist:#e6e6e6;
    --peach-light:#fbd9d3;
    --peach-mid:#f2c0b6;
    --stage:#7c7c7c;
  }
  *{margin:0;padding:0;box-sizing:border-box}
  html,body{width:1200px;height:818px;overflow:hidden;background:var(--stage)}
  .banner{
    position:absolute;left:20px;top:192px;width:1160px;height:434px;
    background:var(--white);overflow:hidden;
    font-family:"Josefin Sans",sans-serif;
  }
  .photo-area{
    position:absolute;left:20px;top:20px;width:1120px;height:395px;border-radius:8px;
    background:linear-gradient(100deg,var(--peach-mid) 0%,var(--peach-light) 60%,#fcdcd7 100%);
  }
  .shapes{position:absolute;left:0;top:0;width:1160px;height:434px}
  .headline{position:absolute;left:57px;color:var(--white);font-weight:700;white-space:nowrap}
  .headline-main{top:38px;font-size:118px;line-height:1;letter-spacing:-1px}
  .headline-sub{top:152px;font-size:70px;line-height:1;left:60px}
  .service{
    position:absolute;height:46px;border-radius:23px;background:var(--charcoal);
    border:3px solid var(--ink);display:flex;align-items:center;
    color:var(--white);font-weight:700;white-space:nowrap;
  }
  .service-dot{width:38px;height:38px;border-radius:50%;background:var(--orange);border:3px solid var(--white);margin-left:1px;flex:none}
  .service-name{font-size:28px;padding-top:5px}
  .service--laser{left:56px;top:231px;width:394px}
  .service--laser .service-name{margin-left:14px;letter-spacing:.5px}
  .service--veluxin{left:56px;top:297px;width:165px}
  .service--veluxin .service-name{margin-left:8px;font-size:26px}
  .service--filler{left:232px;top:297px;width:219px}
  .service--filler .service-name{margin-left:10px}
  .website{position:absolute;left:55px;top:374px;display:flex;align-items:center;gap:14px;color:var(--white)}
  .website-text{font-size:29px;font-weight:600;padding-top:5px;letter-spacing:.3px}
  .brand{position:absolute;left:861px;top:64px;display:flex;align-items:center;gap:12px}
  .brand-dot{width:66px;height:66px;border-radius:50%;background:var(--orange)}
  .brand-name{color:var(--ink);font-weight:700;line-height:1}
  .brand-name span{display:block}
  .brand-name .line-1{font-size:44px}
  .brand-name .line-2{font-size:20px;letter-spacing:2px;margin-top:4px}
  .phone{position:absolute;left:815px;top:378px;display:flex;align-items:center;gap:12px;color:var(--white)}
  .phone-number{font-size:38px;font-weight:700;padding-top:6px;letter-spacing:.5px}
</style>
</head>
<body>
  <div class="banner">
    <div class="photo-area" role="img" aria-label="Photo of two smiling women in white underwear sitting back to back on chairs, legs raised, against a soft peach wall"></div>

    <svg class="shapes" viewBox="0 0 1838 688" preserveAspectRatio="none" aria-hidden="true">
      <path class="footer-bar" fill="var(--charcoal)" d="M32 526 H839 L914 658 H44 Q32 658 32 646 Z"/>
      <path class="accent-band" fill="var(--mist)" d="M32 120 H800 L900 330 Q906 342 900 354 L790 556 Q782 566 765 566 H32 Z"/>
      <path class="headline-panel" fill="var(--orange)" d="M48 32 H757 L890 258 Q898 272 890 286 L770 500 Q762 512 745 512 H32 V48 Q32 32 48 32 Z"/>
      <path class="phone-band" fill="var(--orange)" d="M1274 570 H1838 V688 H1214 Z"/>
    </svg>

    <h1 class="headline headline-main">Refresh</h1>
    <p class="headline headline-sub">YOUR SKIN</p>

    <div class="service service--laser"><span class="service-dot"></span><span class="service-name">LASER HAIR REMOVAL</span></div>
    <div class="service service--veluxin"><span class="service-dot"></span><span class="service-name">VELUXIN</span></div>
    <div class="service service--filler"><span class="service-dot"></span><span class="service-name">LIP FILLER</span></div>

    <div class="website">
      <svg width="36" height="36" viewBox="0 0 36 36" fill="none" stroke="#fff" stroke-width="1.6" stroke-linejoin="round" aria-hidden="true">
        <path d="M31 5 C22 5 15 10 11 18 L18 25 C26 21 31 14 31 5 Z"/>
        <circle cx="22" cy="14" r="2.6"/>
        <path d="M11 18 L6 18 L10 13 L15 13"/>
        <path d="M18 25 L18 30 L23 26 L23 21"/>
        <path d="M9 24 L4 29 M12 27 L8 31 M7 21 L4 24"/>
      </svg>
      <span class="website-text">www.MarlowDermalStudio.com</span>
    </div>

    <div class="brand">
      <span class="brand-dot"></span>
      <p class="brand-name"><span class="line-1">Marlow</span><span class="line-2">Dermal Studio</span></p>
    </div>

    <div class="phone">
      <svg width="38" height="38" viewBox="0 0 38 38" fill="none" stroke="#fff" stroke-width="2" stroke-linecap="round" stroke-linejoin="round" aria-hidden="true">
        <path d="M9 4 L14 10 L11 14 C13 19 17 24 23 27 L27 24 L33 29 L29 34 C17 33 5 21 4 9 Z"/>
        <path d="M21 6 C26 7 30 11 31 16"/>
        <path d="M21 11 C24 12 25 13 26 16"/>
      </svg>
      <span class="phone-number">(520) 867-2291</span>
    </div>
  </div>
</body>
</html>
```